KAJU Freightways #ALLKAJU Business Cards & Letterhead

I am looking to business cards designed for our organization. We are currently undergoing a small re-branding that is taking place. Our organization is called KAJU Freightways and we are headquartered in Phoenix, AZ. We primarily provide transportation and logistics services to the Marlow Parcel Bureau who is our largest customer. I would like to see a design that incorporates name, title, contact info, website, and address (this will be different depending on the employee). I would also like to see some color on the business card using our logo colors or a variation. I would like our logo on the back of the business card with the website displayed. The final design should communicate that we are a next generation transportation operate that focuses on being driver-first, customer-centric, innovative, and sustainable.We would also like our #ALLKAJU catch phrase incorporated as well.

Target Market(s)

Transportation & Logistics

Industry/Entity Type

Trucking Company

Contact Information for Business Card

-First and Last Name
-Position Title
-Contact Phone
-Contact Email
-Physical Address

Font styles to use
Serif

Colors

Designer to choose colors to be used in the design.

Requirements
Must have
• -KAJU logo prominently displayed
• -#ALLKAJU catch phrase used
• -Some amount of color, design gradient, etc.
• -Logo on the back with website listed (https://www.kajufreightco.example)

```html
<!DOCTYPE html>
<html lang="en">
<head>
<meta charset="utf-8">
<title>KAJU Freightways Business Card</title>
<link href="https://fonts.googleapis.com/css2?family=Arimo:wght@400;700&family=Roboto+Condensed:wght@400;500&display=swap" rel="stylesheet">
<style>
  :root {
    --bg: #7b7b7b;
    --teal: #053f4b;
    --teal-mid: #2f6650;
    --green: #7bbd42;
    --ink: #163f4a;
    --grey: #5b5f61;
    --rule: #b9bcbd;
    --white: #ffffff;
  }
  * { box-sizing: border-box; margin: 0; padding: 0; }
  html, body { width: 1200px; height: 675px; overflow: hidden; }
  body {
    background: var(--bg);
    font-family: "Arimo", Arial, sans-serif;
    display: flex;
    align-items: center;
    justify-content: center;
    gap: 40px;
  }
  .card {
    position: relative;
    width: 540px;
    height: 309px;
    border-radius: 16px;
    overflow: hidden;
    box-shadow: 0 8px 20px rgba(0,0,0,0.35);
  }

  /* Back side */
  .card-back {
    background: linear-gradient(35deg, var(--teal) 10%, var(--teal-mid) 45%, var(--green) 92%);
  }
  .card-back .brand {
    position: absolute;
    top: 108px; left: 0; right: 0;
    display: flex; align-items: center; justify-content: center; gap: 14px;
    color: var(--white);
  }
  .brand-dot {
    width: 34px; height: 34px; border-radius: 50%;
    border: 4px solid currentColor;
  }
  .brand-name {
    font-weight: 700; font-size: 58px; letter-spacing: 1px; line-height: 1;
  }
  .card-back .website {
    position: absolute; bottom: 34px; left: 0; right: 0;
    text-align: center; color: var(--white); font-size: 15px;
  }

  /* Front side */
  .card-front { background: var(--white); }
  .card-front .brand {
    position: absolute; top: 100px; left: 48px;
    display: flex; align-items: center; gap: 12px;
    color: var(--ink);
  }
  .card-front .brand-dot { border-color: var(--green); }
  .card-front .brand-name { font-size: 52px; }
  .tagline {
    position: absolute; top: 168px; left: 48px;
    font-family: "Roboto Condensed", "Arial Narrow", sans-serif;
    font-weight: 500; font-size: 15px; color: var(--green);
  }
  .divider {
    position: absolute; left: 292px; top: 48px;
    width: 1px; height: 160px; background: var(--rule);
  }
  .contact {
    position: absolute; left: 310px; top: 50px; right: 16px;
    color: var(--grey); font-size: 11.5px; line-height: 1.45;
  }
  .contact .name { font-weight: 700; font-size: 19px; color: var(--ink); line-height: 1.1; }
  .contact .title { color: var(--green); font-size: 13px; margin-bottom: 8px; }
  .contact .address { margin-bottom: 8px; }
  .contact ul { list-style: none; }
  .contact li { display: flex; align-items: center; gap: 6px; }
  .contact svg { width: 11px; height: 11px; flex: none; }
  .band { position: absolute; left: 0; bottom: 0; width: 540px; height: 309px; }
  .hashtag {
    position: absolute; right: 120px; bottom: 44px;
    color: var(--white); font-weight: 700; font-size: 16px; letter-spacing: 0.5px;
  }
</style>
</head>
<body>

  <section class="card card-back" aria-label="Card back">
    <div class="brand">
      <span class="brand-dot"></span>
      <span class="brand-name">KAJU</span>
    </div>
    <p class="website">www.kajufreightco.example</p>
  </section>

  <section class="card card-front" aria-label="Card front">
    <svg class="band" viewBox="0 0 540 309" aria-hidden="true">
      <defs>
        <linearGradient id="bandFill" x1="0" y1="0" x2="1" y2="0">
          <stop offset="0" stop-color="#053f4b"/>
          <stop offset="0.5" stop-color="#2f6650"/>
          <stop offset="1" stop-color="#7bbd42"/>
        </linearGradient>
      </defs>
      <polygon points="70,244 540,228 540,272 0,292 0,262" fill="url(#bandFill)"/>
    </svg>

    <div class="brand">
      <span class="brand-dot"></span>
      <span class="brand-name">KAJU</span>
    </div>
    <p class="tagline">Transportation and Logistics Services</p>

    <div class="divider"></div>

    <div class="contact">
      <p class="name">RORY VANCE</p>
      <p class="title">President</p>
      <p class="address">4120 North Canyon Ridge Road<br>Mesa, AZ 85201</p>
      <ul>
        <li>
          <svg viewBox="0 0 12 12"><path d="M2.5 1l2 2-1 1.3c.7 1.4 1.8 2.5 3.2 3.2L8 6.5l2 2-1.3 1.7C5 9.8 2.2 7 1.8 2.3z" fill="#7bbd42"/></svg>
          480-555-0142
        </li>
        <li>
          <svg viewBox="0 0 12 12"><rect x="1" y="2.5" width="10" height="7" fill="none" stroke="#7bbd42" stroke-width="1.3"/><path d="M1 2.5l5 4 5-4" fill="none" stroke="#7bbd42" stroke-width="1.3"/></svg>
          info@kajufreightco.example
        </li>
        <li>
          <svg viewBox="0 0 12 12"><circle cx="6" cy="6" r="4.8" fill="none" stroke="#7bbd42" stroke-width="1.2"/><path d="M1.2 6h9.6M6 1.2c2 2.6 2 7 0 9.6M6 1.2c-2 2.6-2 7 0 9.6" fill="none" stroke="#7bbd42" stroke-width="1"/></svg>
          www.kajufreightco.example
        </li>
      </ul>
    </div>

    <p class="hashtag">#ALLKAJU</p>
  </section>

</body>
</html>
```